New website for a business that provides behaviour analysis

A new website that details the services that are provided around behaviour analysis for people with a disability through QPKV. There also needs to incorporate an about us and a staff page, Plus a referral form that is a google doc.
The business already has a web address that needs to be tailored.
Soft colours are preferred.
Do not have lots of pictures, keep them minimal.
A logo for the business is also needed to be incorporated, and this is a separate project that can be awarded to the website winner.
Website needs to be able to be used on WIX who will be the host for the design.

Target Market(s)

QPKV clients requiring behaviour support clician

Industry/Entity Type

Clinical behaviour support and analysis

Colors
00AB8E
00BBA5
67D7C9
C6EFE9
E9F9F6

Requirements
Must have
• Soft colours, preferable pale turquoise, minimal pictures, clean, sophisticated and classical look

```html
<!DOCTYPE html>
<html lang="en">
<head>
<meta charset="utf-8">
<title>CALMORA – Our Doctors</title>
<link rel="stylesheet" href="https://fonts.googleapis.com/css2?family=DM+Serif+Display&family=Work+Sans:wght@400;500;600;700&display=swap">
<style>
:root{
  --teal:#00AB8E;
  --teal-2:#00BBA5;
  --teal-3:#67D7C9;
  --mint:#C6EFE9;
  --mist:#E9F9F6;
  --page:#F7FBFB;
  --ink:#1f2a2a;
  --white:#ffffff;
  --deep:#1e8a76;
}
*{box-sizing:border-box;margin:0;padding:0}
html,body{width:1200px;height:3188px;overflow:hidden}
body{font-family:"Work Sans",sans-serif;background:var(--page);color:var(--ink);position:relative}
.abs{position:absolute}
.serif{font-family:"DM Serif Display",serif}

/* top bar */
.topbar{top:0;left:0;width:1200px;height:70px;background:var(--white)}
.brand{left:165px;top:14px;font-size:33px;color:var(--teal);letter-spacing:.5px;font-family:"DM Serif Display",serif}
.info{top:17px;display:flex;gap:10px;align-items:center}
.info svg{width:30px;height:30px;stroke:var(--teal);fill:none;stroke-width:1.6}
.info b{display:block;font-size:13px;font-weight:500;color:var(--teal);letter-spacing:.4px}
.info span{font-size:13px;color:var(--teal)}

/* nav */
.nav{top:70px;left:0;width:1200px;height:70px;background:var(--teal)}
.nav ul{position:absolute;left:165px;top:26px;display:flex;gap:19px;list-style:none;color:var(--white);font-size:15px}
.nav li.active{font-weight:700}
.search{left:838px;top:24px;width:22px;height:22px;stroke:#fff;fill:none;stroke-width:2}
.appt{left:884px;top:16px;width:152px;height:40px;border-radius:20px;background:var(--white);color:var(--teal);font-size:14px;font-weight:500;display:flex;align-items:center;justify-content:center}

/* hero */
.hero{top:140px;left:0;width:1200px;height:213px;background:linear-gradient(90deg,#b9b0a6 0%,#d8d5d0 35%,#cfcac2 60%,#a9a29a 100%);overflow:hidden}
.hero-arc{left:-70px;top:-110px;width:170px;height:200px;border-radius:50%;background:rgba(103,215,201,.35)}
.crumb{left:165px;top:70px;font-size:15px;color:var(--teal)}
.hero h1{left:165px;top:84px;font-size:48px;font-weight:400;color:var(--teal);font-family:"DM Serif Display",serif}
.hero-rule{top:353px;left:268px;width:932px;height:7px;background:var(--teal)}
.hero-rule-soft{top:353px;left:0;width:268px;height:7px;background:var(--mist)}

/* doctors */
.doctor{width:278px;height:471px;background:var(--mist)}
.doctor .photo{width:278px;height:308px;background:linear-gradient(180deg,#d9d6d3,#c9c5c0 55%,#eeeeee)}
.doctor .name{text-align:center;margin-top:24px;font-size:15px;color:var(--teal)}
.doctor .spec{text-align:center;margin-top:10px;font-size:15px;font-weight:600;letter-spacing:3px;color:var(--teal)}
.socials{display:flex;justify-content:center;gap:19px;margin-top:14px}
.socials i{width:20px;height:20px;border-radius:50%;background:var(--teal);display:block}
.doctor .btn{position:absolute;bottom:0;left:0;width:278px;height:39px;background:var(--teal);color:#fff;font-size:14px;display:flex;align-items:center;justify-content:center}

/* testimonial */
.quote{top:1435px;left:0;width:1200px;height:386px;background:linear-gradient(90deg,#7fd2c2 0%,#5ab9a5 40%,#2f9a84 70%,#238571 100%)}
.quote .mark{left:0;width:1200px;top:6px;text-align:center;font-family:"DM Serif Display",serif;font-size:96px;color:#fff;line-height:1}
.quote p{left:300px;width:600px;top:116px;text-align:center;font-size:19px;line-height:27px;color:#fff}
.quote hr{left:503px;top:242px;width:194px;border:0;border-top:1px solid rgba(255,255,255,.7)}
.quote .who{left:0;width:1200px;top:262px;text-align:center;font-size:19px;color:#fff}
.dots{display:flex;gap:9px;justify-content:center}
.dots i{width:15px;height:15px;border-radius:50%;background:#fff;display:block}

/* section titles */
.kicker{left:0;width:1200px;text-align:center;font-size:15px;font-weight:600;letter-spacing:3.5px;color:var(--teal)}
.title{left:0;width:1200px;text-align:center;font-size:32px;color:var(--teal);font-family:"DM Serif Display",serif}

/* news */
.news{width:426px;height:135px;background:var(--white);box-shadow:0 4px 16px rgba(0,80,70,.05);display:flex}
.news .thumb{width:140px;height:135px;background:linear-gradient(135deg,#1d2326,#4a5257 50%,#c9ccd0)}
.news .body{padding:18px 18px 0 18px}
.news .date{font-size:12px;color:var(--teal)}
.news h3{font-size:16px;font-weight:400;line-height:21px;margin-top:8px;color:var(--ink)}
.stats{display:flex;gap:10px;margin-top:17px;font-size:12px;align-items:center}
.stats span{display:flex;gap:4px;align-items:center}
.stats svg{width:15px;height:13px;fill:none;stroke-width:1.6}
.ndots{left:0;width:1200px;top:2308px;display:flex;justify-content:center;gap:10px}
.ndots i{width:15px;height:15px;border-radius:50%;background:var(--mint);display:block}
.ndots i.on{background:var(--teal)}

/* contact */
.cc{top:2551px;width:204px;height:204px;background:var(--mist);padding:42px 0 0 26px}
.cc svg{width:32px;height:32px;fill:none;stroke:var(--teal);stroke-width:1.6}
.cc h4{margin-top:14px;font-size:15px;font-weight:700;color:var(--teal)}
.cc p{font-size:14px;line-height:24px;color:var(--teal);margin-top:4px}
.cc p small{font-size:12px}
.cc.on{background:var(--teal)}
.cc.on svg{stroke:#fff}
.cc.on h4,.cc.on p{color:#fff}

/* footer */
.footer{top:2812px;left:0;width:1200px;height:376px;background:var(--teal);color:#fff}
.footer .brand{color:#fff;top:60px;left:165px}
.footer .tag{left:165px;top:117px;font-size:16px;line-height:22px}
.fcol{top:66px;font-size:14px}
.fcol h5{font-size:15px;font-weight:600;margin-bottom:22px}
.fcol li{list-style:none;line-height:25.5px}
.mail{left:796px;top:116px;width:239px;height:44px;background:#fff;border-radius:3px;color:var(--teal);font-size:14px;padding:13px 0 0 9px}
.mail svg{position:absolute;right:14px;top:13px;width:20px;height:18px;fill:#1e2b6a}
.fline{left:165px;top:250px;width:870px;border-top:1px solid rgba(255,255,255,.6)}
.copy{left:165px;top:292px;font-size:13px}
.fsoc{left:938px;top:291px;display:flex;gap:19px}
.fsoc i{width:20px;height:20px;border-radius:50%;background:#fff;display:block}
</style>
</head>
<body>

<header class="abs topbar">
  <div class="abs brand">CALMORA</div>
  <div class="abs info" style="left:490px">
    <svg viewBox="0 0 30 30"><path d="M9 5l4 5-2.5 2.5a14 14 0 0 0 7 7L20 17l5 4-2.5 3.5C14 25 5 16 5.5 7.5z"/><path d="M17 5a8 8 0 0 1 8 8M17 9a4 4 0 0 1 4 4"/></svg>
    <div><b>EMERGENCY</b><span>(555) 014-2290</span></div>
  </div>
  <div class="abs info" style="left:666px">
    <svg viewBox="0 0 30 30"><circle cx="15" cy="15" r="12"/><path d="M15 8v7l4 4"/></svg>
    <div><b>WORK HOUR</b><span>09:00 - 20:00 Everyday</span></div>
  </div>
  <div class="abs info" style="left:882px">
    <svg viewBox="0 0 30 30"><path d="M15 27s9-8.5 9-15a9 9 0 0 0-18 0c0 6.5 9 15 9 15z"/><circle cx="15" cy="12" r="3.5"/></svg>
    <div><b>LOCATION</b><span>0123 Some Place</span></div>
  </div>
</header>

<nav class="abs nav">
  <ul>
    <li>Home</li><li>About us</li><li>Services</li><li class="active">Doctors</li><li>News</li><li>Contact</li>
  </ul>
  <svg class="abs search" viewBox="0 0 22 22"><circle cx="9.5" cy="9.5" r="7.5"/><path d="M15 15l5 5"/></svg>
  <div class="abs appt">Appointment</div>
</nav>

<section class="abs hero" role="img" aria-label="Group photo of the clinical team in white coats in front of a building">
  <div class="abs hero-arc"></div>
  <div class="abs crumb">Home / Doctors</div>
  <h1 class="abs">Our Doctors</h1>
</section>
<div class="abs hero-rule-soft"></div>
<div class="abs hero-rule"></div>

<!-- doctors grid -->
<article class="abs doctor" style="left:165px;top:416px"><div class="photo" role="img" aria-label="Portrait of a smiling doctor in a white coat with stethoscope"></div><div class="name">Doctor’s Name</div><div class="spec">NEUROLOGY</div><div class="socials"><i></i><i></i><i></i></div><div class="btn">View Profile</div></article>
<article class="abs doctor" style="left:460px;top:416px"><div class="photo" role="img" aria-label="Portrait of a doctor with arms crossed in a clinic room"></div><div class="name">Doctor’s Name</div><div class="spec">NEUROLOGY</div><div class="socials"><i></i><i></i><i></i></div><div class="btn">View Profile</div></article>
<article class="abs doctor" style="left:757px;top:416px"><div class="photo" role="img" aria-label="Portrait of a doctor in a white coat in a bright office"></div><div class="name">Doctor’s Name</div><div class="spec">NEUROLOGY</div><div class="socials"><i></i><i></i><i></i></div><div class="btn">View Profile</div></article>
<article class="abs doctor" style="left:165px;top:907px"><div class="photo" role="img" aria-label="Portrait of a smiling doctor in a white coat with stethoscope"></div><div class="name">Doctor’s Name</div><div class="spec">NEUROLOGY</div><div class="socials"><i></i><i></i><i></i></div><div class="btn">View Profile</div></article>
<article class="abs doctor" style="left:460px;top:907px"><div class="photo" role="img" aria-label="Portrait of a doctor with arms crossed in a clinic room"></div><div class="name">Doctor’s Name</div><div class="spec">NEUROLOGY</div><div class="socials"><i></i><i></i><i></i></div><div class="btn">View Profile</div></article>
<article class="abs doctor" style="left:757px;top:907px"><div class="photo" role="img" aria-label="Portrait of a doctor in a white coat in a bright office"></div><div class="name">Doctor’s Name</div><div class="spec">NEUROLOGY</div><div class="socials"><i></i><i></i><i></i></div><div class="btn">View Profile</div></article>

<!-- testimonial -->
<section class="abs quote" role="img" aria-label="Teal-tinted photo of a doctor holding a stethoscope behind a client testimonial">
  <div class="abs mark">”</div>
  <p class="abs">Lorem ipsum dolor sit amet, consectetur adipiscing elit. Quisque placerat scelerisque tortor ornare ornare. Quisque placerat scelerisque felis vitae tortor augue. Velit nascetur Consequat faucibus porttitor enim et.</p>
  <hr class="abs">
  <div class="abs who">John Doe</div>
  <div class="abs dots" style="left:0;width:1200px;top:315px"><i></i><i></i><i></i></div>
</section>

<!-- news -->
<div class="abs kicker" style="top:1879px">BETTER INFORMATION, BETTER HEALTH</div>
<h2 class="abs title" style="top:1898px;font-weight:400">News</h2>

<article class="abs news" style="left:165px;top:1992px"><div class="thumb" role="img" aria-label="Clinician examining a patient"></div><div class="body"><div class="date">Monday 05, September 2021 | By Author</div><h3>This Article’s Title goes Here,<br>but not too long.</h3><div class="stats"><span><svg viewBox="0 0 16 12" stroke="#4a63d8"><path d="M1 6s3-5 7-5 7 5 7 5-3 5-7 5-7-5-7-5z"/><circle cx="8" cy="6" r="2"/></svg>68</span><span><svg viewBox="0 0 16 14" stroke="#e0455a"><path d="M8 13S1 8.5 1 4.5A3.5 3.5 0 0 1 8 3a3.5 3.5 0 0 1 7 1.5C15 8.5 8 13 8 13z"/></svg>86</span></div></div></article>
<article class="abs news" style="left:609px;top:1992px"><div class="thumb" role="img" aria-label="Clinician examining a patient"></div><div class="body"><div class="date">Monday 05, September 2021 | By Author</div><h3>This Article’s Title goes Here,<br>but not too long.</h3><div class="stats"><span><svg viewBox="0 0 16 12" stroke="#4a63d8"><path d="M1 6s3-5 7-5 7 5 7 5-3 5-7 5-7-5-7-5z"/><circle cx="8" cy="6" r="2"/></svg>68</span><span><svg viewBox="0 0 16 14" stroke="#e0455a"><path d="M8 13S1 8.5 1 4.5A3.5 3.5 0 0 1 8 3a3.5 3.5 0 0 1 7 1.5C15 8.5 8 13 8 13z"/></svg>86</span></div></div></article>
<article class="abs news" style="left:165px;top:2145px"><div class="thumb" role="img" aria-label="Clinician examining a patient"></div><div class="body"><div class="date">Monday 05, September 2021 | By Author</div><h3>This Article’s Title goes Here,<br>but not too long.</h3><div class="stats"><span><svg viewBox="0 0 16 12" stroke="#4a63d8"><path d="M1 6s3-5 7-5 7 5 7 5-3 5-7 5-7-5-7-5z"/><circle cx="8" cy="6" r="2"/></svg>68</span><span><svg viewBox="0 0 16 14" stroke="#e0455a"><path d="M8 13S1 8.5 1 4.5A3.5 3.5 0 0 1 8 3a3.5 3.5 0 0 1 7 1.5C15 8.5 8 13 8 13z"/></svg>86</span></div></div></article>
<article class="abs news" style="left:609px;top:2145px"><div class="thumb" role="img" aria-label="Clinician examining a patient"></div><div class="body"><div class="date">Monday 05, September 2021 | By Author</div><h3>This Article’s Title goes Here,<br>but not too long.</h3><div class="stats"><span><svg viewBox="0 0 16 12" stroke="#4a63d8"><path d="M1 6s3-5 7-5 7 5 7 5-3 5-7 5-7-5-7-5z"/><circle cx="8" cy="6" r="2"/></svg>68</span><span><svg viewBox="0 0 16 14" stroke="#e0455a"><path d="M8 13S1 8.5 1 4.5A3.5 3.5 0 0 1 8 3a3.5 3.5 0 0 1 7 1.5C15 8.5 8 13 8 13z"/></svg>86</span></div></div></article>
<div class="abs ndots"><i></i><i class="on"></i><i></i></div>

<!-- contact -->
<div class="abs kicker" style="top:2438px">GET IN TOUCH</div>
<h2 class="abs title" style="top:2457px;font-weight:400">Contact</h2>

<div class="abs cc" style="left:165px">
  <svg viewBox="0 0 32 32"><path d="M9 6l4 5-2.5 2.5a14 14 0 0 0 7 7L20 18l5 4-2.5 3.5C14 26 5 17 5.5 8.5z"/><path d="M18 6a8 8 0 0 1 8 8M18 10a4 4 0 0 1 4 4"/></svg>
  <h4>EMERGENCY</h4><p>(555) 014-2290<br>(555) 017-3348</p>
</div>
<div class="abs cc on" style="left:387px">
  <svg viewBox="0 0 32 32"><path d="M16 29s10-9 10-16a10 10 0 0 0-20 0c0 7 10 16 10 16z"/><circle cx="16" cy="13" r="4"/></svg>
  <h4>LOCATION</h4><p>0123 Some place<br>9876 Some country</p>
</div>
<div class="abs cc" style="left:609px">
  <svg viewBox="0 0 32 32"><rect x="3" y="7" width="26" height="19"/><path d="M3 7l13 11L29 7"/></svg>
  <h4>EMAIL</h4><p>hello@calmora.example<br><small>team@calmora.example</small></p>
</div>
<div class="abs cc" style="left:831px">
  <svg viewBox="0 0 32 32"><circle cx="16" cy="16" r="13"/><path d="M16 8v8l4 5"/></svg>
  <h4>WORKING HOURS</h4><p>Mon-Sat 09:00-20:00<br>Sunday Emergency only</p>
</div>

<!-- footer -->
<footer class="abs footer">
  <div class="abs brand">CALMORA</div>
  <div class="abs tag">Leading the Way in Medical<br>Execellence, Trusted Care.</div>
  <div class="abs fcol" style="left:406px"><h5>Important Links</h5><ul><li>Appointment</li><li>Doctors</li><li>Services</li><li>About Us</li></ul></div>
  <div class="abs fcol" style="left:560px"><h5>Contact Us</h5><ul><li>Call: (555) 014-2290</li><li>Email: hello@calmora.example</li><li>Address: 0123 Some place</li><li>Some country</li></ul></div>
  <div class="abs fcol" style="left:796px"><h5>Newsletter</h5></div>
  <div class="abs mail">Enter your email address<svg viewBox="0 0 20 18"><path d="M0 8L20 0l-6 18-4-7z"/></svg></div>
  <div class="abs fline"></div>
  <div class="abs copy">© 2021 Hospital’s name All Rights Reserved by Larkfield Studio</div>
  <div class="abs fsoc"><i></i><i></i><i></i></div>
</footer>

</body>
</html>
```